Redesign a Start-Up Dating Website

Website: https://morvelique.com.
Make sure the design has an island style theme.
I would like the 7 pages of my website to have a new and professional look. I want the same colors to remain, but I want a creative look for all the pages. This is a dating website that is in the startup stage. So, I want to give my entire website a custom makeover. I want something that will stand out from the other dating sites. Something that will attract more people to want to use my services, and hopefully get new members.
Target Market(s)
Dating
Industry/Entity Type
Dating
Coding
Coded - Design and coding required
Number of Pages Required
5+ page
Font styles to use
Other font styles liked:
- Decorative, San Serif
Requirements
Must have
- The design must have the original colors and a stylish font to go along. The design must be creative, welcoming, and professional. I would like an island style theme for the website. This is a dating website so make sure that the design is tailored to that aspect.
Nice to have
- It would be nice to have a decorative font and a professional style on all the pages. Make sure the design will be mobile responsive and friendly for all the pages on the website.
Should not have
- The design should not be bland and uncreative.

```html
<!DOCTYPE html>
<html lang="en">
<head>
<meta charset="utf-8">
<title>Morvelique – Find Your Perfect Match</title>
<link rel="stylesheet" href="https://fonts.googleapis.com/css2?family=Roboto:wght@300;400;500;700&family=Roboto+Slab:wght@700&display=swap">
<style>
:root{
  --orange:#f7941d;
  --teal:#2fb5a3;
  --teal-dark:#1f9483;
  --purple:#6b3fa0;
  --purple-dark:#563285;
  --ink:#333842;
  --muted:#8a8f98;
  --line:#e3e5e8;
  --paper:#ffffff;
  --soft:#f5f6f7;
}
*{box-sizing:border-box;margin:0;padding:0}
html,body{width:1200px;height:2928px;overflow:hidden}
body{font-family:"Roboto",Arial,sans-serif;color:var(--ink);background:var(--paper);position:relative}
.section{position:absolute;left:0;width:1200px}

/* header */
.site-header{top:0;height:128px;background:var(--paper)}
.top-tabs{position:absolute;right:96px;top:0;display:flex;gap:2px}
.top-tabs span{background:var(--orange);color:#fff;font-size:11px;font-weight:500;padding:5px 14px;border-radius:0 0 6px 6px;letter-spacing:.5px}
.brand{position:absolute;left:56px;top:44px;display:flex;align-items:center;gap:12px}
.brand-dot{width:46px;height:46px;border-radius:50%;background:var(--orange)}
.brand-name{font-size:36px;font-weight:700;color:var(--orange)}
.main-nav{position:absolute;right:150px;top:62px;display:flex;gap:26px}
.main-nav a{font-size:12.5px;font-weight:500;color:var(--ink);text-decoration:none;letter-spacing:.4px}
.main-nav a.active{color:var(--orange)}
.header-social{position:absolute;right:56px;top:52px;display:flex;gap:8px}
.header-social span{width:34px;height:34px;border-radius:50%;background:var(--purple)}

/* hero */
.hero{top:128px;height:528px}
.hero-photo{position:absolute;inset:0;background:linear-gradient(100deg,#6f8f9c 0%,#a8c3cc 35%,#d9e4e6 60%,#b89a80 100%)}
.quick-search{position:absolute;left:112px;top:64px;width:256px;height:328px;background:rgba(255,255,255,.95);box-shadow:0 4px 16px rgba(0,0,0,.2);padding:22px 20px;text-align:center}
.quick-search h2{font-size:24px;font-weight:700;color:var(--ink)}
.quick-search p{font-size:11px;color:var(--muted);margin:6px 0 18px}
.field-row{display:flex;gap:8px;margin-bottom:12px}
.field{flex:1;height:34px;border:1px solid var(--line);background:#fff;font-size:10px;color:var(--muted);text-align:left;padding:10px 8px;position:relative}
.field::after{content:"";position:absolute;right:8px;top:14px;border:4px solid transparent;border-top-color:var(--muted)}
.search-btn{margin:16px auto 0;width:140px;height:38px;background:var(--purple);color:#fff;font-size:13px;font-weight:700;letter-spacing:1px;line-height:38px}
.hero-title{position:absolute;left:480px;top:100px;font-family:"Roboto Slab",Georgia,serif;font-size:36px;color:#fff;text-shadow:0 2px 6px rgba(0,0,0,.35)}
.hero-arrow{position:absolute;left:400px;top:150px}
.hero-dots{position:absolute;left:568px;top:428px;display:flex;gap:8px}
.hero-dots span{width:10px;height:10px;border-radius:50%;background:rgba(255,255,255,.6)}
.hero-dots span:first-child{background:#fff}
.hero-curve{position:absolute;left:0;bottom:0}

/* profiles */
.section-title{font-size:30px;font-weight:500;text-align:center;letter-spacing:1px;color:var(--ink)}
.profiles{top:700px;height:420px}
.profiles .section-title{margin-top:12px}
.profile-box{position:absolute;left:112px;top:66px;width:976px;height:308px;border:1px solid var(--line);background:#fff;box-shadow:0 2px 8px rgba(0,0,0,.06);display:flex;justify-content:space-around;padding:24px 24px}
.profile-card{width:160px;text-align:center;border:1px solid var(--line);padding-bottom:10px}
.profile-photo{height:160px}
.profile-card h3{font-size:12px;font-weight:700;margin-top:12px}
.profile-card p{font-size:10.5px;color:var(--muted);margin-top:4px}
.profile-card .more{display:inline-block;margin-top:14px;font-size:10px;font-weight:700;color:var(--purple)}
.carousel-arrow{position:absolute;top:208px;font-size:22px;color:var(--muted)}

/* how to join */
.join{top:1180px;height:500px}
.join-photo{position:absolute;inset:0;background:linear-gradient(90deg,#5a3a1c 0%,#c77a2a 35%,#f2b04a 60%,#e79a3c 100%)}
.join-panel{position:absolute;left:480px;top:60px;width:620px;height:380px;background:#fff;box-shadow:0 6px 24px rgba(0,0,0,.25);padding:38px 30px 0}
.join-panel .section-title{font-size:26px}
.steps{display:flex;justify-content:space-between;margin-top:36px}
.step{width:172px;text-align:center}
.step-icon{width:92px;height:92px;border-radius:50%;background:var(--teal);margin:0 auto;display:flex;align-items:center;justify-content:center;box-shadow:0 0 0 6px #d6f0ec}
.step h3{font-size:13px;font-weight:700;color:var(--teal-dark);margin-top:22px;letter-spacing:.4px}
.step p{font-size:11px;color:var(--muted);line-height:1.5;margin-top:8px}

/* news */
.news{top:1760px;height:520px}
.news .section-title{margin-top:0}
.news-grid{position:absolute;left:100px;top:72px;width:1000px;display:grid;grid-template-columns:1fr 1fr;column-gap:32px;row-gap:28px}
.news-item{display:flex;gap:18px;border:1px solid var(--line);background:#fff;height:180px}
.news-photo{width:200px;flex:none}
.news-body{padding:14px 14px 0 0}
.news-body h3{font-size:16px;font-weight:700}
.news-meta{display:flex;gap:10px;margin-top:8px;font-size:10px;color:var(--teal-dark)}
.news-body p{font-size:11px;color:var(--muted);line-height:1.6;margin-top:10px}

/* footer */
.site-footer{top:2300px;height:628px;background:var(--purple)}
.footer-curve{position:absolute;left:0;top:0}
.footer-col{position:absolute;top:120px;color:#fff}
.footer-col h4{font-size:22px;font-weight:500;margin-bottom:22px}
.about-col{left:100px;width:420px}
.about-inner{display:flex;gap:18px}
.about-photo{width:110px;height:110px;flex:none;border:3px solid #fff}
.about-inner p{font-size:11.5px;line-height:1.7;color:#e6dcf2}
.contact-col{left:630px;width:240px}
.contact-line{display:flex;gap:10px;font-size:11.5px;line-height:1.6;color:#e6dcf2;margin-bottom:14px}
.contact-line svg{flex:none;margin-top:2px}
.connect-col{left:900px;width:200px}
.social-row{display:flex;gap:12px}
.social-row span{width:34px;height:34px;border-radius:50%;border:2px solid #fff}
.newsletter{position:absolute;left:100px;top:420px;width:1000px;display:flex;align-items:center;gap:22px}
.newsletter h4{color:#fff;font-size:18px;font-weight:500;letter-spacing:.5px}
.newsletter .input{width:300px;height:38px;background:#fff;font-size:11px;color:var(--muted);padding:12px}
.newsletter .btn{height:38px;background:var(--orange);color:#fff;font-size:12px;font-weight:700;padding:0 24px;line-height:38px;margin-left:-22px}
.footer-brand{margin-left:auto;display:flex;align-items:center;gap:10px}
.footer-brand .brand-dot{width:40px;height:40px}
.footer-brand .brand-name{color:#fff;font-size:32px}
.footer-rule{position:absolute;left:100px;top:494px;width:1000px;height:1px;background:rgba(255,255,255,.25)}
.footer-nav{position:absolute;left:0;top:530px;width:1200px;display:flex;justify-content:center;gap:22px}
.footer-nav a{font-size:11px;color:#fff;text-decoration:none;letter-spacing:.5px}
.copyright{position:absolute;left:0;top:570px;width:1200px;text-align:center;font-size:11px;color:#d9cdea}
</style>
</head>
<body>

<header class="section site-header">
  <div class="top-tabs"><span>LOG IN</span><span>REGISTER</span><span>LANGUAGE</span></div>
  <div class="brand"><span class="brand-dot"></span><span class="brand-name">Morvelique</span></div>
  <nav class="main-nav">
    <a class="active" href="#">HOME</a><a href="#">SEARCH</a><a href="#">MEMBERS</a><a href="#">ZONAS</a><a href="#">ABOUT</a><a href="#">PREMIUM</a><a href="#">CONTACT</a>
  </nav>
  <div class="header-social"><span></span><span></span></div>
</header>

<section class="section hero">
  <div class="hero-photo" role="img" aria-label="Smiling couple on a sunny beach, man carrying woman on his back"></div>
  <form class="quick-search">
    <h2>Quick search</h2>
    <p>Let's Find Your Perfect Match Today</p>
    <div class="field-row"><div class="field">I AM</div><div class="field">SEEKING A</div></div>
    <div class="field-row"><div class="field">AGE</div><div class="field">TO</div></div>
    <div class="field-row"><div class="field">LOCATION</div></div>
    <div class="search-btn">SEARCH</div>
  </form>
  <svg class="hero-arrow" width="90" height="90" viewBox="0 0 90 90"><path d="M80 10 C40 10 20 40 24 76" fill="none" stroke="#fff" stroke-width="3"/><path d="M14 64 L24 78 L34 64" fill="none" stroke="#fff" stroke-width="3"/></svg>
  <h1 class="hero-title">Find Your Perfect Match For Free!</h1>
  <div class="hero-dots"><span></span><span></span><span></span><span></span></div>
  <svg class="hero-curve" width="1200" height="40" viewBox="0 0 1200 40"><path d="M0 40 L0 14 Q600 44 1200 4 L1200 40 Z" fill="#fff"/><path d="M0 14 Q600 44 1200 4" fill="none" stroke="var(--teal)" stroke-width="5"/></svg>
</section>

<section class="section profiles">
  <h2 class="section-title">LAST ADDED PROFILES</h2>
  <span class="carousel-arrow" style="left:92px">&#8249;</span>
  <span class="carousel-arrow" style="right:92px">&#8250;</span>
  <div class="profile-box">
    <div class="profile-card"><div class="profile-photo" role="img" aria-label="Member portrait" style="background:linear-gradient(#c9b39c,#8d7663)"></div><h3>LUIS MONTERO</h3><p>Age: 32 · Kingston</p><span class="more">VIEW INFO ›</span></div>
    <div class="profile-card"><div class="profile-photo" role="img" aria-label="Member portrait" style="background:linear-gradient(#d7c8b8,#9f8877)"></div><h3>CORALBOO</h3><p>Age: 28 · Nassau</p><span class="more">VIEW INFO ›</span></div>
    <div class="profile-card"><div class="profile-photo" role="img" aria-label="Member portrait" style="background:linear-gradient(#e3dad0,#a89787)"></div><h3>LEON MARTIN</h3><p>Age: 35 · Bridgetown</p><span class="more">VIEW INFO ›</span></div>
    <div class="profile-card"><div class="profile-photo" role="img" aria-label="Member portrait" style="background:linear-gradient(#8c6a52,#4f3a2c)"></div><h3>SEABREEZE</h3><p>Age: 26 · Castries</p><span class="more">VIEW INFO ›</span></div>
    <div class="profile-card"><div class="profile-photo" role="img" aria-label="Member portrait" style="background:linear-gradient(#c0a892,#7d6656)"></div><h3>DAVID RAMOS</h3><p>Age: 30 · Montego</p><span class="more">VIEW INFO ›</span></div>
  </div>
</section>

<section class="section join">
  <div class="join-photo" role="img" aria-label="Couple embracing at sunset on the beach"></div>
  <div class="join-panel">
    <h2 class="section-title">HOW TO JOIN US ?</h2>
    <div class="steps">
      <div class="step">
        <div class="step-icon"><svg width="40" height="40" viewBox="0 0 40 40"><rect x="6" y="8" width="24" height="26" rx="2" fill="none" stroke="#fff" stroke-width="3"/><path d="M16 24 L32 6 L36 10 L20 28 L14 30 Z" fill="#fff"/></svg></div>
        <h3>CREATE A PROFILE</h3>
        <p>Sign up in minutes and tell others who you are and what you seek.</p>
      </div>
      <div class="step">
        <div class="step-icon"><svg width="40" height="40" viewBox="0 0 40 40"><circle cx="17" cy="17" r="11" fill="none" stroke="#fff" stroke-width="4"/><path d="M25 25 L35 35" stroke="#fff" stroke-width="5" stroke-linecap="round"/></svg></div>
        <h3>FIND MATCHES</h3>
        <p>Browse island singles near you and find the people you like.</p>
      </div>
      <div class="step">
        <div class="step-icon"><svg width="40" height="40" viewBox="0 0 40 40"><path d="M20 35 C6 25 3 18 3 12 A8.5 8.5 0 0 1 20 9 A8.5 8.5 0 0 1 37 12 C37 18 34 25 20 35 Z" fill="#fff"/></svg></div>
        <h3>START DATING</h3>
        <p>Send a message, plan a meet and let the romance begin today.</p>
      </div>
    </div>
  </div>
</section>

<section class="section news">
  <h2 class="section-title">LATEST NEWS</h2>
  <div class="news-grid">
    <article class="news-item">
      <div class="news-photo" role="img" aria-label="Couple hugging outdoors" style="background:linear-gradient(135deg,#d9b79a,#8a6a55)"></div>
      <div class="news-body"><h3>Island dates under the sun</h3><div class="news-meta"><span>By Admin</span><span>Apr 12</span><span>3 Comments</span></div><p>Simple ideas for a first date by the sea, from sunset walks to beach picnics that help you relax and get to know each other well.</p></div>
    </article>
    <article class="news-item">
      <div class="news-photo" role="img" aria-label="Couple sitting close together" style="background:linear-gradient(135deg,#b7a79a,#5f5048)"></div>
      <div class="news-body"><h3>Accessories for couples</h3><div class="news-meta"><span>By Admin</span><span>Apr 09</span><span>5 Comments</span></div><p>Small matching gifts can say a lot. Here are a few thoughtful pieces to share with your partner on a special day together.</p></div>
    </article>
    <article class="news-item">
      <div class="news-photo" role="img" aria-label="Couple laughing together" style="background:linear-gradient(135deg,#e0c4b0,#9c7a66)"></div>
      <div class="news-body"><h3>Tips for a great profile</h3><div class="news-meta"><span>By Admin</span><span>Apr 04</span><span>2 Comments</span></div><p>A clear photo and an honest short bio make a big difference. Learn how to stand out and attract the right kind of match.</p></div>
    </article>
    <article class="news-item">
      <div class="news-photo" role="img" aria-label="Couple walking in a sunny field" style="background:linear-gradient(135deg,#e6c48e,#a3784a)"></div>
      <div class="news-body"><h3>Planning your first trip</h3><div class="news-meta"><span>By Admin</span><span>Mar 28</span><span>4 Comments</span></div><p>Ready to travel together? Our guide covers calm beaches, local food and quiet spots perfect for couples on the islands.</p></div>
    </article>
  </div>
</section>

<footer class="section site-footer">
  <svg class="footer-curve" width="1200" height="60" viewBox="0 0 1200 60"><path d="M0 0 L1200 0 L1200 20 Q600 70 0 30 Z" fill="#fff"/><path d="M0 30 Q600 70 1200 20" fill="none" stroke="var(--teal)" stroke-width="5"/></svg>
  <div class="footer-col about-col">
    <h4>About Us</h4>
    <div class="about-inner">
      <div class="about-photo" role="img" aria-label="Happy couple portrait" style="background:linear-gradient(135deg,#e0b98f,#9a6f4c)"></div>
      <p>Morvelique aims to provide a simple, friendly way to meet other island singles. We believe every person deserves a partner who shares their dreams, and we help you connect with real people who care about the same things you do.</p>
    </div>
  </div>
  <div class="footer-col contact-col">
    <h4>Get in touch</h4>
    <div class="contact-line"><svg width="14" height="16" viewBox="0 0 14 16"><path d="M7 0 A6 6 0 0 1 13 6 C13 10 7 16 7 16 C7 16 1 10 1 6 A6 6 0 0 1 7 0 Z" fill="#fff"/><circle cx="7" cy="6" r="2.2" fill="var(--purple)"/></svg><span>Harbor Lane, 14 Coral Road,<br>Palm Bay, Isla Verde</span></div>
    <div class="contact-line"><svg width="14" height="14" viewBox="0 0 14 14"><path d="M3 0 L6 4 L4 6 C5 8 6 9 8 10 L10 8 L14 11 L12 14 C6 14 0 8 0 2 Z" fill="#fff"/></svg><span>Phone : 0100 555 0184</span></div>
    <div class="contact-line"><svg width="16" height="12" viewBox="0 0 16 12"><rect x="0.5" y="0.5" width="15" height="11" fill="none" stroke="#fff"/><path d="M1 1 L8 7 L15 1" fill="none" stroke="#fff"/></svg><span>Email : hello@morvelique.com</span></div>
  </div>
  <div class="footer-col connect-col">
    <h4>Stay Connected</h4>
    <div class="social-row"><span></span><span></span><span></span><span></span></div>
  </div>
  <div class="newsletter">
    <h4>NEWSLETTER SIGN UP</h4>
    <div class="input">Enter Email...</div>
    <div class="btn">SIGN UP NOW</div>
    <div class="footer-brand"><span class="brand-dot"></span><span class="brand-name">Morvelique</span></div>
  </div>
  <div class="footer-rule"></div>
  <nav class="footer-nav"><a href="#">ABOUT</a><a href="#">CONTACT</a><a href="#">ZONAS</a><a href="#">MEMBERS</a><a href="#">PREMIUM</a><a href="#">REGISTER</a><a href="#">SEARCH</a></nav>
  <p class="copyright">© Copyright 2017 Morvelique Dating. All Rights Reserved.</p>
</footer>

</body>
</html>
```